Business card for a Exhibition booth fabrication company

Hi. My company would like to change our corporate name card. We are an events and Exhibition stand builder company. We would like our corporate name card to resonate what we do. I need someone to create something unique that relates to the industry that I am in. The graphic designer should be creative to incorporate the elements of my industry and try to blend in well in the design of the card. Our aim is to ensure that we are unique and our card can look different from our competitors.
Updates

Target Market(s)

Marketing and events manager from all companies

Contact Information for Business Card

The business card should have the following details:
Name
Job Title
Email
Website

Colors

Designer to choose colors to be used in the design.

Requirements
Must have
• The card must be look something that is relevant to the service that I am providing. My website is: www.velmora-buildworks.com
• You can see my website to get more information on what service that I am doing
Nice to have
• On the back of my card, I would like to have a globe image with the incorporation of my company logo. This is to indicate that my services can be done in any part of the world.

```html
<!DOCTYPE html>
<html lang="en">
<head>
<meta charset="UTF-8">
<title>Velmora Buildworks – Business Card</title>
<link href="https://fonts.googleapis.com/css2?family=Work+Sans:wght@400;500;600&display=swap" rel="stylesheet">
<style>
  :root {
    --page-bg: #161616;
    --card-bg: #232323;
    --card-bg-edge: #1c1c1c;
    --accent-red: #e3242b;
    --text-light: #f2f2f2;
    --text-silver: #a9a9a9;
  }
  * { margin: 0; padding: 0; box-sizing: border-box; }
  html, body {
    width: 1200px;
    height: 900px;
    overflow: hidden;
    background: var(--page-bg);
    font-family: "Work Sans", Arial, sans-serif;
  }
  .stage {
    position: relative;
    width: 1200px;
    height: 900px;
  }
  .card {
    position: absolute;
    left: 250px;
    width: 700px;
    height: 400px;
    background: linear-gradient(160deg, var(--card-bg) 0%, var(--card-bg-edge) 100%);
  }
  .card--front { top: 40px; }
  .card--back { top: 460px; }

  /* Front */
  .front-brand {
    position: absolute;
    inset: 0;
    display: flex;
    align-items: center;
    justify-content: center;
  }
  .front-brand__name {
    font-weight: 600;
    font-size: 30px;
    letter-spacing: 4px;
    color: var(--text-silver);
    text-transform: uppercase;
  }

  /* Back */
  .back-brand {
    position: absolute;
    left: 40px;
    top: 0;
    width: 320px;
    height: 100%;
    display: flex;
    align-items: center;
    gap: 12px;
  }
  .back-brand__dot {
    width: 16px;
    height: 16px;
    border-radius: 50%;
    background: var(--accent-red);
    flex: none;
  }
  .back-brand__name {
    font-weight: 600;
    font-size: 21px;
    letter-spacing: 2.5px;
    color: var(--text-light);
    text-transform: uppercase;
    white-space: nowrap;
  }
  .divider {
    position: absolute;
    left: 390px;
    top: 95px;
    width: 2px;
    height: 220px;
    background: var(--accent-red);
  }
  .contact {
    position: absolute;
    left: 415px;
    top: 100px;
    color: var(--text-light);
  }
  .contact__name {
    font-size: 27px;
    font-weight: 500;
    color: var(--accent-red);
    letter-spacing: 1px;
    text-transform: uppercase;
    line-height: 1.1;
    white-space: nowrap;
  }
  .contact__title {
    font-size: 16px;
    margin-top: 2px;
    letter-spacing: 0.5px;
  }
  .contact__address {
    font-size: 15px;
    margin-top: 14px;
    line-height: 1.4;
    letter-spacing: 0.4px;
  }
  .contact__list {
    list-style: none;
    margin-top: 8px;
    font-size: 15px;
    letter-spacing: 0.4px;
  }
  .contact__list li {
    display: flex;
    align-items: center;
    gap: 8px;
    line-height: 1.5;
    white-space: nowrap;
  }
  .contact__icon {
    width: 12px;
    height: 12px;
    flex: none;
    stroke: var(--accent-red);
    fill: none;
    stroke-width: 1.6;
  }
</style>
</head>
<body>
<main class="stage">
  <section class="card card--front" aria-label="Card front">
    <div class="front-brand">
      <span class="front-brand__name">Velmora Buildworks</span>
    </div>
  </section>

  <section class="card card--back" aria-label="Card back">
    <div class="back-brand">
      <span class="back-brand__dot"></span>
      <span class="back-brand__name">Velmora Buildworks</span>
    </div>
    <div class="divider"></div>
    <div class="contact">
      <h1 class="contact__name">Daniel Hart</h1>
      <p class="contact__title">Director</p>
      <p class="contact__address">P.O. Box 4821 Al Noor<br>Street Doha - Qatar</p>
      <ul class="contact__list">
        <li>
          <svg class="contact__icon" viewBox="0 0 12 12"><path d="M2 1.5 L4 1.5 L5 4 L3.8 5 Q5 7.5 7 8.2 L8 7 L10.5 8 L10.5 10 Q6 10.5 3.5 7.5 Q1.5 5 2 1.5 Z"/></svg>
          +65 81047726
        </li>
        <li>
          <svg class="contact__icon" viewBox="0 0 12 12"><rect x="3" y="1" width="6" height="10" rx="1"/><line x1="5" y1="9" x2="7" y2="9"/></svg>
          +974 55208841
        </li>
        <li>
          <svg class="contact__icon" viewBox="0 0 12 12"><rect x="1" y="2.5" width="10" height="7"/><polyline points="1,2.5 6,6.5 11,2.5"/></svg>
          info@velmora-buildworks.com
        </li>
        <li>
          <svg class="contact__icon" viewBox="0 0 12 12"><circle cx="6" cy="6" r="5"/><ellipse cx="6" cy="6" rx="2.2" ry="5"/><line x1="1" y1="6" x2="11" y2="6"/></svg>
          www.velmora-buildworks.com
        </li>
      </ul>
    </div>
  </section>
</main>
</body>
</html>
```